Baby Boutique Needs a Business Card Design

We need a modern double sided business card design using the attached logo for Little Wren Nook.

Little Wren Nook is a baby boutique which sells only handmade clothing and accessories for both boys and girls. Our store will live exclusively online.

We would like to only use the colors that have been used in the logo.

Target Market(s)

Potential wholesale clients, Small business owners

Industry/Entity Type

Retail

Contact Information for Business Card

Name Gideon R. Falkner (Owner)
Email sales@littlewrennook.example
Main Phone 555-203-7719
Cell phone 555-203-7746
Website www.LittleWrenNook.example

Font styles to use
Sans Serif

Colors

Designer to choose colors to be used in the design.

Requirements
Must have
• -Would like to have icons that indentify the contact information.
• -Include our website
• -Include our tagline in a small area near the bottom. "Handmade Baby Creations"
• -Would like to include Facebook and Instagram Icons
• -
Nice to have
• Would like to have a simple back side with the logo.
• Something along the lines of the meadowfield lending card attached.

```html
<!DOCTYPE html>
<html lang="en">
<head>
<meta charset="utf-8">
<title>Little Wren Nook — Business Card</title>
<link rel="stylesheet" href="https://fonts.googleapis.com/css2?family=Lato:wght@400;700;900&display=swap">
<style>
  :root {
    --backdrop: #3d3532;
    --card: #2a2628;
    --teal: #6fd8c6;
    --coral: #e8625e;
    --ink-light: #ece9ea;
    --ink-dark: #2a2628;
  }
  * { box-sizing: border-box; margin: 0; padding: 0; }
  html, body {
    width: 1200px; height: 716px; overflow: hidden;
    background: var(--backdrop);
    font-family: "Lato", sans-serif;
  }
  .canvas {
    position: relative; width: 1200px; height: 716px;
    display: flex; align-items: center; justify-content: center; gap: 40px;
  }
  .card {
    position: relative; width: 540px; height: 309px;
    background: var(--card);
    border-radius: 4px;
    box-shadow: 0 10px 30px rgba(0,0,0,0.35);
    overflow: hidden;
  }
  .brand-name {
    font-family: "Lato", sans-serif;
    font-weight: 900;
    color: var(--teal);
    line-height: 1.02;
    text-align: center;
  }
  /* back side */
  .card-back { display: flex; align-items: center; justify-content: center; }
  .card-back .brand-name { font-size: 50px; }
  /* front side */
  .card-front .brand {
    position: absolute; left: 30px; top: 70px; width: 230px;
    display: flex; flex-direction: column; align-items: center; gap: 12px;
  }
  .card-front .brand-name { font-size: 38px; }
  .brand-dot {
    width: 12px; height: 12px; border-radius: 50%; background: var(--coral);
  }
  .divider {
    position: absolute; left: 283px; top: 52px;
    width: 2px; height: 168px; background: var(--teal);
  }
  .contact { position: absolute; left: 312px; top: 62px; color: var(--ink-light); }
  .contact-name { color: var(--coral); font-weight: 700; font-size: 19px; }
  .contact-role { font-size: 12px; margin-top: 2px; margin-bottom: 20px; }
  .contact-list { list-style: none; }
  .contact-list li {
    display: flex; align-items: center; gap: 9px;
    font-size: 14px; line-height: 19px;
  }
  .contact-list svg { width: 11px; height: 11px; flex: none; }
  .social-dot {
    width: 11px; height: 11px; border-radius: 50%; background: var(--coral); flex: none;
  }
  .band-line {
    position: absolute; left: 0; right: 0; bottom: 44px;
    height: 3px; background: var(--coral);
  }
  .band {
    position: absolute; left: 0; right: 0; bottom: 0; height: 44px;
    background: var(--teal);
    display: flex; align-items: center; padding-left: 72px;
  }
  .tagline { color: var(--ink-dark); font-size: 13px; font-weight: 700; letter-spacing: 0.2px; }
</style>
</head>
<body>
<main class="canvas">
  <section class="card card-back" aria-label="Card back">
    <p class="brand-name">Little Wren<br>Nook</p>
  </section>

  <section class="card card-front" aria-label="Card front">
    <div class="brand">
      <p class="brand-name">Little Wren<br>Nook</p>
      <span class="brand-dot"></span>
    </div>
    <div class="divider"></div>
    <div class="contact">
      <p class="contact-name">Gideon R. Falkner</p>
      <p class="contact-role">Owner</p>
      <ul class="contact-list">
        <li>
          <svg viewBox="0 0 12 12"><path d="M3 1 L5 3.5 L4 5 Q5.5 7 7 8 L8.5 7 L11 9 L9.5 11 Q5 10.5 1 3 Z" fill="var(--coral)"/></svg>
          555-203-7719
        </li>
        <li>
          <svg viewBox="0 0 12 12"><rect x="3" y="0.8" width="6" height="10.4" rx="1.2" fill="none" stroke="var(--coral)" stroke-width="1.3"/><circle cx="6" cy="9.3" r="0.7" fill="var(--coral)"/></svg>
          555-203-7746
        </li>
        <li>
          <svg viewBox="0 0 12 12"><rect x="0.8" y="2.5" width="10.4" height="7" fill="none" stroke="var(--coral)" stroke-width="1.2"/><path d="M1 3 L6 7 L11 3" fill="none" stroke="var(--coral)" stroke-width="1.2"/></svg>
          sales@littlewrennook.example
        </li>
        <li>
          <svg viewBox="0 0 12 12"><circle cx="6" cy="6" r="5" fill="none" stroke="var(--coral)" stroke-width="1.2"/><ellipse cx="6" cy="6" rx="2.2" ry="5" fill="none" stroke="var(--coral)" stroke-width="1"/><path d="M1 6 H11" stroke="var(--coral)" stroke-width="1"/></svg>
          www.LittleWrenNook.example
        </li>
        <li>
          <span class="social-dot"></span>
          /LittleWrenNook
        </li>
      </ul>
    </div>
    <div class="band-line"></div>
    <div class="band"><p class="tagline">Handmade Baby Creations</p></div>
  </section>
</main>
</body>
</html>
```